Restyle corporate identity (+ logo) for a road construction company

We need a new logo and stationary design for our company VARNOK path. VARNOK path® increases the road base strength, while reducing major costs and time of road construction. Attached some examples of the current design.

Our wishes for the new logo:
- Business look
- Style sheet
- Modern

More information: www.varnokpath.example
Updates

Target Market(s)

Government

Industry/Entity Type

Construction

Requirements
Must have
• Logo (with road sign) + text

```html
<!DOCTYPE html>
<html lang="en">
<head>
<meta charset="utf-8">
<title>VARNOK path – Business Card</title>
<link rel="stylesheet" href="https://fonts.googleapis.com/css2?family=Open+Sans:wght@400;600&display=swap">
<style>
  :root {
    --backdrop: #8c8c8c;
    --card: #eeeeee;
    --brand-blue: #0b7ddf;
    --rule-grey: #9c9c9c;
    --ink: #4a4a4a;
    --on-blue: #ffffff;
  }
  * { margin: 0; padding: 0; box-sizing: border-box; }
  html, body {
    width: 1105px; height: 1200px; overflow: hidden;
    background: var(--backdrop);
    font-family: "Open Sans", Arial, sans-serif;
  }
  .card {
    position: absolute; left: 182px; width: 746px; height: 427px;
    background: var(--card); overflow: hidden;
  }
  .card--front { top: 119px; }
  .card--back { top: 637px; }

  .brand {
    position: absolute; display: flex; align-items: center; gap: 16px;
    color: var(--brand-blue); font-weight: 600; letter-spacing: 2px;
  }
  .card--front .brand { left: 39px; top: 64px; font-size: 44px; }
  .brand__square { background: var(--brand-blue); flex: none; }
  .card--front .brand__square { width: 56px; height: 56px; border-radius: 8px; }

  .band { position: absolute; left: 0; top: 0; width: 746px; height: 427px; }

  .holder {
    position: absolute; right: 39px; top: 244px; text-align: right; color: var(--on-blue);
  }
  .holder__name { font-size: 26px; font-weight: 600; line-height: 1.1; letter-spacing: .5px; }
  .holder__role { font-size: 19px; line-height: 1.5; }

  .address {
    position: absolute; left: 39px; top: 315px; color: var(--on-blue);
    font-size: 19px; line-height: 28.5px; list-style: none;
  }
  .contacts {
    position: absolute; right: 39px; top: 315px; color: var(--on-blue);
    font-size: 19px; line-height: 28.5px; list-style: none; text-align: right;
  }
  .contacts li { display: flex; justify-content: flex-end; align-items: center; gap: 8px; }
  .contacts svg { width: 17px; height: 17px; flex: none; }

  .card--back .brand {
    left: 0; right: 0; top: 150px; justify-content: center;
    font-size: 58px; gap: 20px;
  }
  .card--back .brand__square { width: 72px; height: 72px; border-radius: 12px; }
  .back-url {
    position: absolute; left: 0; right: 0; top: 355px; text-align: center;
    color: var(--ink); font-size: 19px; letter-spacing: 7px;
  }
</style>
</head>
<body>
  <section class="card card--front">
    <div class="brand"><span class="brand__square"></span><span>VARNOK PATH</span></div>

    <svg class="band" viewBox="0 0 746 427" aria-hidden="true">
      <polygon points="0,240 420,240 410,250 0,250" fill="var(--rule-grey)"/>
      <polygon points="0,251 411,251 446,217 746,217 746,427 0,427" fill="var(--brand-blue)"/>
    </svg>

    <div class="holder">
      <p class="holder__name">MAREN OSTERLOH</p>
      <p class="holder__role">CEO/Founder</p>
    </div>

    <ul class="address">
      <li>Lindenkade 57</li>
      <li>2514 KL Veldhaven</li>
      <li>The Netherlands</li>
    </ul>

    <ul class="contacts">
      <li>610 555 0147
        <svg viewBox="0 0 24 24" aria-hidden="true"><path fill="#fff" d="M6.6 10.8a15.2 15.2 0 0 0 6.6 6.6l2.2-2.2a1 1 0 0 1 1-.25 11.4 11.4 0 0 0 3.6.57 1 1 0 0 1 1 1V20a1 1 0 0 1-1 1A17 17 0 0 1 3 4a1 1 0 0 1 1-1h3.5a1 1 0 0 1 1 1c0 1.25.2 2.45.57 3.57a1 1 0 0 1-.25 1z"/></svg>
      </li>
      <li>hello@varnokpath.example
        <svg viewBox="0 0 24 24" aria-hidden="true"><rect x="2" y="5" width="20" height="14" rx="1.5" fill="#fff"/><path d="M3 6l9 7 9-7" fill="none" stroke="var(--brand-blue)" stroke-width="1.6"/></svg>
      </li>
      <li>www.varnokpath.example
        <svg viewBox="0 0 24 24" aria-hidden="true"><circle cx="12" cy="12" r="10" fill="#fff"/><path d="M2 12h20M12 2c3 3 3 17 0 20M12 2c-3 3-3 17 0 20" fill="none" stroke="var(--brand-blue)" stroke-width="1.4"/></svg>
      </li>
    </ul>
  </section>

  <section class="card card--back">
    <div class="brand"><span class="brand__square"></span><span>VARNOK PATH</span></div>
    <p class="back-url">www.varnokpath.example</p>
  </section>
</body>
</html>
```